Business Card Design for Varomir Facility Services

We are looking for a Business Card Design for the Company "Varomir Facility Services."
Front side:
- Company Logo (small)
- Company Name, address, pohone, website and personal data.
- white background, for text e.g. company colors (blue or green like in the logo)
Please use following data:
Company data:
Varomir Facility Services Kostelac
Birkenhaldweg 14
6330 Cham
www.varomir-fs.ch
Person data:
Tarik Kostelac
Geschäftsführer
+41 76 519 47 83
info@varomir-fs.ch
Back side:
could be colored in blue or green
please use a big logo sing and some smaller icons to say what is all beeing offered in facility services, like cleaning, maintenance cleaning
industrial cleaning, caretaking, gardening, disposal. There is no need for everyone of the icons if there are similar or an icon is standing for more of them.
colors to use:
blue: HEX 246BB0
green: HEX 52B33E

```html
<!DOCTYPE html>
<html lang="de">
<head>
<meta charset="utf-8">
<title>Varomir Facility Services – Visitenkarte</title>
<link rel="stylesheet" href="https://fonts.googleapis.com/css2?family=Poppins:wght@400;600&display=swap">
<style>
  :root {
    --brand-blue: #246bb0;
    --card-blue: #0052b0;
    --name-blue: #0a55b0;
    --brand-green: #52b33e;
    --text-grey: #555a60;
    --rule-grey: #c9ccd0;
    --paper: #ffffff;
    --stage: #e9eaec;
  }
  * { box-sizing: border-box; margin: 0; padding: 0; }
  html, body {
    width: 1125px; height: 1200px; overflow: hidden;
    background: var(--stage);
    font-family: "Poppins", sans-serif;
  }
  .canvas { position: relative; width: 1125px; height: 1200px; }

  .card {
    position: absolute; left: 150px; width: 826px; height: 471px;
    box-shadow: 0 3px 8px rgba(0,0,0,.25);
  }
  .card--front { top: 98px; background: var(--paper); }
  .card--back  { top: 631px; background: var(--card-blue); }

  /* front */
  .brand-mark {
    position: absolute; left: 55px; top: 180px; width: 330px;
    display: flex; align-items: center; gap: 14px;
  }
  .brand-mark__dot {
    flex: none; width: 26px; height: 26px; border-radius: 50%;
    background: var(--brand-green);
  }
  .brand-mark__name {
    font-weight: 600; font-size: 34px; line-height: 1.15;
    color: var(--brand-blue);
  }
  .divider {
    position: absolute; left: 405px; top: 108px; width: 1px; height: 264px;
    background: linear-gradient(to bottom, transparent, var(--rule-grey) 15%, var(--rule-grey) 85%, transparent);
  }
  .contact { position: absolute; left: 435px; top: 112px; }
  .contact__name {
    font-weight: 600; font-size: 31px; line-height: 1.2; color: var(--name-blue);
  }
  .contact__role {
    font-size: 20px; line-height: 1.2; color: var(--brand-green); margin-bottom: 8px;
  }
  .contact__address {
    font-size: 20px; line-height: 1.23; color: var(--text-grey);
    font-style: normal; margin-bottom: 10px;
  }
  .contact__list { list-style: none; }
  .contact__item {
    display: flex; align-items: center; gap: 10px;
    font-size: 20px; line-height: 1.3; color: var(--text-grey);
  }
  .contact__icon { width: 19px; height: 19px; flex: none; }

  /* back */
  .brand-mark--large {
    position: absolute; left: 0; right: 0; top: 150px;
    display: flex; align-items: center; justify-content: center; gap: 20px;
  }
  .brand-mark--large .brand-mark__dot { width: 40px; height: 40px; }
  .brand-mark--large .brand-mark__name {
    font-size: 52px; color: var(--paper); text-align: left;
  }
  .services {
    position: absolute; left: 0; right: 0; top: 376px;
    text-align: center; color: var(--paper);
    font-size: 20.5px; line-height: 1.2;
  }
</style>
</head>
<body>
<div class="canvas">

  <section class="card card--front" aria-label="Vorderseite">
    <div class="brand-mark">
      <span class="brand-mark__dot"></span>
      <span class="brand-mark__name">Varomir<br>Facility Services</span>
    </div>

    <div class="divider"></div>

    <div class="contact">
      <h1 class="contact__name">Tarik Kostelac</h1>
      <p class="contact__role">Geschäftsführer</p>
      <address class="contact__address">
        Varomir Facility Services Kostelac<br>
        Birkenhaldweg 14<br>
        6330 Cham
      </address>
      <ul class="contact__list">
        <li class="contact__item">
          <svg class="contact__icon" viewBox="0 0 20 20" aria-hidden="true">
            <rect x="5" y="1" width="10" height="18" rx="2" fill="none" stroke="var(--name-blue)" stroke-width="2"/>
            <rect x="7.5" y="15" width="5" height="1.6" fill="var(--name-blue)"/>
          </svg>
          +41 76 519 47 83
        </li>
        <li class="contact__item">
          <svg class="contact__icon" viewBox="0 0 20 20" aria-hidden="true">
            <rect x="2" y="5" width="16" height="11" fill="var(--name-blue)"/>
            <path d="M2 5 L10 11 L18 5" fill="none" stroke="#fff" stroke-width="1.4"/>
          </svg>
          info@varomir-fs.ch
        </li>
        <li class="contact__item">
          <svg class="contact__icon" viewBox="0 0 20 20" aria-hidden="true">
            <circle cx="10" cy="10" r="8" fill="var(--name-blue)"/>
            <path d="M6 6 q3 1 2 4 q-2 1 -1 4 M12 4 q-1 3 2 4 q2 2 1 5" fill="none" stroke="#fff" stroke-width="1.4"/>
          </svg>
          www.varomir-fs.ch
        </li>
      </ul>
    </div>
  </section>

  <section class="card card--back" aria-label="Rückseite">
    <div class="brand-mark brand-mark--large">
      <span class="brand-mark__dot"></span>
      <span class="brand-mark__name">Varomir<br>Facility Services</span>
    </div>
    <p class="services">
      Cleaning | Maintenance cleaning | Industrial cleaning<br>
      Caretaking | Gardening | Disposal
    </p>
  </section>

</div>
</body>
</html>
```